Business Card Design

New business card design

Target Market(s)

Residential & Commercial Property Managers

Industry/Entity Type

Plumbing Services

Contact Information for Business Card

Name - Rowan Keddle, title - Director, Phone Number - 0431 286 517, email - rowan@tbk-plumbing.com.au, Company ABN - 73 215 904 386,

Font styles to use
Sans Serif

Colors
0054AA
0677BA
7BADD7
CADEEF
E8F1F8

```html
<!DOCTYPE html>
<html lang="en">
<head>
<meta charset="utf-8">
<title>TBK Plumbing Services – Business Card</title>
<link href="https://fonts.googleapis.com/css2?family=Montserrat:wght@400;500;700&display=swap" rel="stylesheet">
<style>
  :root {
    --ink: #1d232c;
    --water: #29a8e0;
    --paper: #ffffff;
    --stage: #e7e4df;
  }
  * { box-sizing: border-box; margin: 0; padding: 0; }
  html, body {
    width: 900px; height: 1200px; overflow: hidden;
    background: var(--stage);
    font-family: "Montserrat", sans-serif;
  }
  .canvas { position: relative; width: 900px; height: 1200px; }

  .card {
    position: absolute;
    width: 742px; height: 442px;
    border-radius: 24px;
    overflow: hidden;
    box-shadow: 0 10px 24px rgba(0,0,0,0.18);
  }
  .card--front { left: 80px; top: 130px; background: var(--paper); }
  .card--back  { left: 79px; top: 638px; background: var(--ink); }

  /* company name: one font, one weight, one colour */
  .company-name {
    position: absolute;
    font-weight: 500;
    text-align: center;
    line-height: 1.2;
  }
  .card--front .company-name {
    left: 40px; width: 300px; top: 182px;
    font-size: 30px; color: var(--ink);
  }
  .card--back .company-name {
    left: 0; right: 0; top: 168px;
    font-size: 48px; color: var(--paper);
  }

  .divider {
    position: absolute; left: 367px; top: 127px;
    width: 2px; height: 181px; background: var(--ink);
  }

  .contact { position: absolute; left: 388px; top: 126px; color: var(--ink); }
  .contact__name { font-size: 26px; font-weight: 700; line-height: 1.1; }
  .contact__title { font-size: 15px; font-weight: 500; margin-top: 3px; }
  .contact__list { list-style: none; margin-top: 16px; }
  .contact__item {
    display: flex; align-items: center; gap: 9px;
    font-size: 15.5px; font-weight: 500; height: 31px;
  }
  .contact__item svg { width: 17px; height: 17px; fill: var(--ink); flex: none; }
  .contact__abn { display: block; line-height: 31px; }
  .contact__abn strong { font-weight: 700; }

  .band { position: absolute; height: 31px; top: 375px; }
  .band--ink { left: 0; width: 345px; background: var(--ink); }
  .band--water { left: 395px; right: 0; background: var(--water); height: 30px; }
</style>
</head>
<body>
<main class="canvas">

  <section class="card card--front" aria-label="Business card front">
    <p class="company-name">TBK<br>Plumbing Services</p>

    <div class="divider"></div>

    <div class="contact">
      <h1 class="contact__name">Rowan Keddle</h1>
      <p class="contact__title">Director</p>
      <ul class="contact__list">
        <li class="contact__item">
          <svg viewBox="0 0 24 24" aria-hidden="true"><path d="M6.6 10.8a15 15 0 0 0 6.6 6.6l2.2-2.2c.3-.3.7-.4 1-.2 1.1.4 2.3.6 3.6.6.6 0 1 .4 1 1V20c0 .6-.4 1-1 1C10.6 21 3 13.4 3 4c0-.6.4-1 1-1h3.5c.6 0 1 .4 1 1 0 1.3.2 2.5.6 3.6.1.3 0 .7-.2 1z"/></svg>
          0431 286 517
        </li>
        <li class="contact__item">
          <svg viewBox="0 0 24 24" aria-hidden="true"><path d="M3 5h18v2l-9 6-9-6z"/><path d="M3 9l9 6 9-6v10H3z"/></svg>
          rowan@tbk-plumbing.com.au
        </li>
        <li class="contact__item">
          <svg viewBox="0 0 24 24" aria-hidden="true"><path d="M12 2a10 10 0 1 0 0 20 10 10 0 0 0 0-20zm0 2c.9 0 2.2 1.8 2.8 5H9.2C9.8 5.8 11.1 4 12 4zM4.3 10h3.8a18 18 0 0 0 0 4H4.3a8 8 0 0 1 0-4zm5 0h5.4a16 16 0 0 1 0 4H9.3a16 16 0 0 1 0-4zm6.6 0h3.8a8 8 0 0 1 0 4h-3.8a18 18 0 0 0 0-4zM9.2 15h5.6c-.6 3.2-1.9 5-2.8 5s-2.2-1.8-2.8-5z"/></svg>
          www.tbk-plumbing.com.au
        </li>
        <li class="contact__item contact__abn"><strong>ABN</strong> - 73 215 904 386</li>
      </ul>
    </div>

    <div class="band band--ink"></div>
    <div class="band band--water"></div>
  </section>

  <section class="card card--back" aria-label="Business card back">
    <p class="company-name">TBK<br>Plumbing Services</p>
  </section>

</main>
</body>
</html>
```